KESTREL Academy Exhibit Booth Posters

My company is KESTREL Academy (a division of KESTREL for Growth). We are exhibiting in a month, and I need to re-do my exhibit booth posters. There will be a total of 4 posters needed. Sizes are below.
1) Top- 11 feet long X 12 inches wide (Try to match color scheme in example photo)
2) Center- 4 feet long X 2 feet wide (Chalkboard background)
3) Left- 18 inches long X 2 feet wide (Cork-board back ground with the use of push pins holding up post-it-notes, paper, etc.)
4) Right- 18 inches long X 2 feet wide (Cork-board back ground with the use of push pins holding up post-it-notes, paper, etc.)
I have attached a photo of my old booth. This will get you an idea of the size, color schemes, and more. I have created basic rendering of each poster. The content is important, but the look and design should be drastically improved.
The websites to look into for ideas are:
www.kestrelforgrowth.example
www.kestrelacademy.example
Updates
I've added a new file. It's a .JPG of the certification diploma. Thanks!
Target Market(s)
Business Owners, Managers, HR, Supervisors, Teens who want to boost their resume
Industry/Entity Type
It Company
Look and feel

```html
<!DOCTYPE html>
<html lang="en">
<head>
<meta charset="utf-8">
<title>KESTREL Academy — Top Booth Banner</title>
<link rel="stylesheet" href="https://fonts.googleapis.com/css2?family=Cabin+Sketch:wght@400;700&display=swap">
<style>
  :root {
    --board-dark: #232323;
    --board-mid: #3b3b3b;
    --board-edge: #1b1b1b;
    --chalk: #f1f1ee;
    --chalk-soft: #e4e4e0;
  }
  html, body {
    margin: 0;
    padding: 0;
    width: 1200px;
    height: 100px;
    overflow: hidden;
    background: var(--board-dark);
  }
  .banner {
    display: block;
    width: 1200px;
    height: 100px;
  }
  .brand-name {
    font-family: "Cabin Sketch", cursive;
    font-weight: 700;
    fill: var(--chalk);
  }
  .brand-mark {
    fill: none;
    stroke: var(--chalk);
    stroke-width: 2.5;
  }
  .banner-title {
    font-family: "Cabin Sketch", cursive;
    font-weight: 700;
    fill: var(--chalk);
  }
  .banner-tagline {
    font-family: "Cabin Sketch", cursive;
    font-weight: 700;
    fill: var(--chalk-soft);
  }
</style>
</head>
<body>
<svg class="banner" viewBox="0 0 1200 100" xmlns="http://www.w3.org/2000/svg">
  <defs>
    <radialGradient id="chalkboard-wash" cx="50%" cy="45%" r="65%">
      <stop offset="0%" stop-color="var(--board-mid)"/>
      <stop offset="70%" stop-color="var(--board-dark)"/>
      <stop offset="100%" stop-color="var(--board-edge)"/>
    </radialGradient>
  </defs>

  <rect class="chalkboard" role="img" aria-label="Chalkboard surface with faint chalk smudges"
        x="0" y="0" width="1200" height="100" fill="url(#chalkboard-wash)"/>

  <g class="brand">
    <circle class="brand-mark" cx="26" cy="50" r="14"/>
    <text class="brand-name" x="48" y="56" font-size="16" textLength="112" lengthAdjust="spacingAndGlyphs">KESTREL Academy</text>
  </g>

  <text class="banner-title" x="176" y="66" font-size="66"
        textLength="974" lengthAdjust="spacingAndGlyphs">KESTREL ACADEMY</text>

  <text class="banner-tagline" x="200" y="92" font-size="19"
        textLength="876" lengthAdjust="spacingAndGlyphs">TRAINING SCHOOL FOR A WORKFORCE WITH LIMITED WORK EXPERIANCE</text>
</svg>
</body>
</html>
```